Maple Roster Business Card for recruitment company

We are looking for a Business Card Design that incorporates our personal details and our busines name and logo. We are a specialized search consultancy that recruit Property and Construction professionals.
We would like a business card that stands out and is appealing to the Construction and Property industry as well.

Target Market(s)

people in the construction and property industry

Contact Information for Business Card

Business Name and logo

Font styles to use
Serif

Colors
0094D4
00A9DD
6FCCEA
C7EBF8
E9F6FB

Requirements
Must have
• Business name and logo as well as contact details
Should not have
• No photos of us please

```html
<!DOCTYPE html>
<html lang="en">
<head>
<meta charset="utf-8">
<title>Maple Roster Business Card</title>
<link href="https://fonts.googleapis.com/css2?family=Lato:wght@300;400;700&display=swap" rel="stylesheet">
<style>
  :root {
    --page: #e4e4e4;
    --paper: #ffffff;
    --teal: #005a6b;
    --teal-deep: #00354a;
    --teal-light: #006d7e;
    --ink: #1d1d1d;
    --muted: #6b6b6b;
    --emboss: #002a3c;
  }
  * { margin: 0; padding: 0; box-sizing: border-box; }
  html, body {
    width: 1200px; height: 1200px; overflow: hidden;
    background: var(--page);
    font-family: "Lato", Arial, sans-serif;
  }
  .card {
    position: absolute; left: 262px; width: 686px; height: 392px;
  }
  .card-front { top: 165px; background: var(--paper); }
  .card-front .base-band {
    position: absolute; left: 0; right: 0; bottom: 0; height: 10px;
    background: linear-gradient(90deg, var(--teal-deep), var(--teal-light));
  }
  .brand-name {
    position: absolute; white-space: nowrap; font-weight: 400;
  }
  .card-front .brand-name {
    left: 77px; width: 274px; top: 201px; transform: translateY(-50%);
    font-size: 36px; letter-spacing: 0.3px; color: var(--teal);
    text-align: center;
  }
  .divider {
    position: absolute; left: 379px; top: 99px; height: 195px;
    border-left: 2px dashed var(--teal);
  }
  .details { position: absolute; left: 408px; top: 96px; }
  .person-name {
    font-size: 24px; font-weight: 700; color: var(--teal);
    letter-spacing: 0.3px; line-height: 1.1;
  }
  .person-role { font-size: 15.5px; color: var(--ink); margin-top: 1px; }
  .address {
    font-size: 15.5px; color: var(--muted); margin-top: 13px; line-height: 19px;
  }
  .contact-list { list-style: none; margin-top: 9px; }
  .contact-list li {
    display: flex; align-items: center; gap: 9px;
    font-size: 15.5px; color: var(--muted); line-height: 19.5px;
  }
  .contact-list svg { width: 13px; height: 13px; fill: var(--teal); flex: none; }
  .card-back {
    top: 653px;
    background: linear-gradient(35deg, #00293d 0%, #003e55 45%, #006878 100%);
  }
  .card-back .brand-name {
    left: 50%; top: 50%; transform: translate(-50%, -50%);
    font-size: 62px; color: var(--emboss); letter-spacing: 1px;
  }
</style>
</head>
<body>
  <section class="card card-front">
    <div class="brand-name">MAPLE ROSTER</div>
    <div class="divider"></div>
    <div class="details">
      <div class="person-name">DANIEL HART</div>
      <div class="person-role">President</div>
      <div class="address">4120 Cedar Hollow Road<br>Juneau, Alaska 99801</div>
      <ul class="contact-list">
        <li><svg viewBox="0 0 16 16"><path d="M3 1l3 3-1.5 2c1 2 3 4 5 5L11.5 9.5l3 3L13 15C7 15 1 9 1 3z"/></svg>555-214-7730</li>
        <li><svg viewBox="0 0 16 16"><path d="M4 0h8v16H4zM5.5 2v10h5V2zM7 13h2v2H7z" fill-rule="evenodd"/></svg>555-608-1942</li>
        <li><svg viewBox="0 0 16 16"><path d="M4 1h8v4H4zM1 6h14v6h-2v3H3v-3H1zM5 10v3h6v-3z" fill-rule="evenodd"/></svg>555-377-4051</li>
        <li><svg viewBox="0 0 16 16"><path d="M1 3h14v10H1zM2.5 4.5L8 8.5l5.5-4z" fill-rule="evenodd"/></svg>daniel@mapleroster.com</li>
        <li><svg viewBox="0 0 16 16"><circle cx="8" cy="8" r="7"/><path d="M4 4c2 1 1 3 3 3s1 3 3 3M10 3c0 2 2 2 3 3" stroke="#fff" stroke-width="1.2" fill="none"/></svg>www.mapleroster.com</li>
      </ul>
    </div>
    <div class="base-band"></div>
  </section>

  <section class="card card-back">
    <div class="brand-name">MAPLE ROSTER</div>
  </section>
</body>
</html>
```